Fitness Equipment Repair Business Needs a Catchy New Business Card

We have an existing business card, however, it is quite plain and boring. We are expanding primarily in the commercial area (gyms, studios, apartment complexes etc). The business card will serve as eye candy to those managers/owners that can't be met for a face to face.
Originally I was planning for a brochure as well, but all of our information is better summarized on our website. (brightloopservice.ca).
I would like the card to match the colour scheme of the website and utilize the logo. It should have a professional clean feel to it, however, a little colouring outside the lines wouldn't hurt.
The example card is for my service technician (Colin Marsh). If possible I would like to be able to edit the text to use for more than one person.

Industry/Entity Type

Appliance Repair

Contact Information for Business Card

Clean, crisp and professional but needs to be eye catching. Preferably using the black, white and red colour scheme matching the website. Double sided would be nice, but is not necessary.

Colors
ec1f27
ffffff
000000

Requirements
Must have
• Must be able to edit name, phone number and title to use for multiple people. Must show the company website (brightloopservice.ca).

```html
<!DOCTYPE html>
<html lang="en">
<head>
<meta charset="utf-8">
<title>Brightloop Service – Business Card</title>
<link rel="stylesheet" href="https://fonts.googleapis.com/css2?family=Cinzel:wght@500;700&family=Open+Sans:ital,wght@0,400;1,700&display=swap">
<style>
  :root {
    --brand-red: #ec1f27;
    --ink: #000000;
    --paper: #ffffff;
    --muted: #e4e4e4;
    --backdrop: #e6e3df;
  }
  * { margin: 0; padding: 0; box-sizing: border-box; }
  html, body {
    width: 1200px; height: 987px; overflow: hidden;
    background: var(--backdrop);
  }
  .canvas { position: relative; width: 1200px; height: 987px; }
  .card {
    position: absolute; left: 292px; width: 616px; height: 351px;
    box-shadow: 0 4px 14px rgba(0,0,0,.25);
    overflow: hidden;
  }
  .card--front { top: 130px; background: var(--ink); color: var(--paper); }
  .card--back { top: 506px; background: var(--brand-red); color: var(--paper); }

  .brand {
    position: absolute; left: 130px; top: 58px;
    display: flex; align-items: center; gap: 22px;
  }
  .brand__dot {
    width: 70px; height: 70px; border-radius: 50%;
    background: var(--brand-red);
  }
  .brand__name {
    font-family: "Cinzel", serif; font-weight: 500;
    font-size: 21px; letter-spacing: 1px; color: var(--paper);
  }

  .person {
    position: absolute; right: 339px; top: 192px; text-align: right;
    font-family: "Open Sans", sans-serif;
  }
  .person__name {
    font-family: "Cinzel", serif; font-weight: 700;
    font-size: 20px; color: var(--brand-red); letter-spacing: 1px; line-height: 26px;
  }
  .person__title {
    font-family: "Cinzel", serif; font-weight: 500;
    font-size: 15px; color: var(--muted); letter-spacing: 1px; line-height: 22px;
  }
  .person__address { margin-top: 8px; font-size: 16px; line-height: 23px; }

  .contacts {
    position: absolute; left: 310px; top: 196px; list-style: none;
    font-family: "Open Sans", sans-serif; font-size: 16px; line-height: 23.5px;
  }
  .contacts li { display: flex; align-items: center; gap: 7px; }
  .contacts svg { width: 13px; height: 13px; fill: var(--brand-red); flex: none; }

  .tagline-band {
    position: absolute; left: 0; right: 0; bottom: 0; height: 35px;
    background: var(--brand-red); border-top: 4px solid var(--paper);
    display: flex; align-items: center; justify-content: center;
    font-family: "Open Sans", sans-serif; font-style: italic; font-weight: 700;
    font-size: 15.5px; color: var(--paper); white-space: nowrap;
  }

  .back-brand {
    position: absolute; left: 0; right: 0; top: 72px;
    display: flex; flex-direction: column; align-items: center; gap: 20px;
  }
  .back-brand__dot {
    width: 130px; height: 130px; border-radius: 50%;
    border: 2px solid var(--paper);
  }
  .back-brand__name {
    font-family: "Cinzel", serif; font-weight: 700;
    font-size: 30px; letter-spacing: 2px; color: var(--paper);
  }
  .back-url {
    position: absolute; left: 0; right: 0; top: 306px; text-align: center;
    font-family: "Cinzel", serif; font-weight: 500;
    font-size: 15px; letter-spacing: 2.5px; color: var(--paper);
  }
</style>
</head>
<body>
<main class="canvas">
  <section class="card card--front">
    <div class="brand">
      <span class="brand__dot"></span>
      <span class="brand__name">Brightloop Service</span>
    </div>

    <div class="person">
      <p class="person__name">Colin Marsh</p>
      <p class="person__title">Service technician</p>
      <p class="person__address">1185 Calder Lane NW<br>Edmonton AB T6R 2K4</p>
    </div>

    <ul class="contacts">
      <li><svg viewBox="0 0 24 24"><path d="M6.6 10.8a15 15 0 0 0 6.6 6.6l2.2-2.2c.3-.3.7-.4 1-.2 1.1.4 2.3.6 3.6.6.6 0 1 .4 1 1V20c0 .6-.4 1-1 1A17 17 0 0 1 3 4c0-.6.4-1 1-1h3.5c.6 0 1 .4 1 1 0 1.3.2 2.5.6 3.6.1.3 0 .7-.2 1z"/></svg>587-555-0142(Personal)</li>
      <li><svg viewBox="0 0 24 24"><path d="M6.6 10.8a15 15 0 0 0 6.6 6.6l2.2-2.2c.3-.3.7-.4 1-.2 1.1.4 2.3.6 3.6.6.6 0 1 .4 1 1V20c0 .6-.4 1-1 1A17 17 0 0 1 3 4c0-.6.4-1 1-1h3.5c.6 0 1 .4 1 1 0 1.3.2 2.5.6 3.6.1.3 0 .7-.2 1z"/></svg>780-555-0187(Service Line)</li>
      <li><svg viewBox="0 0 24 24"><path d="M2 5h20v2l-10 7L2 7z M2 9.5l10 7 10-7V19H2z"/></svg>hello@brightloopservice.ca</li>
      <li><svg viewBox="0 0 24 24"><path d="M12 2a10 10 0 1 0 0 20 10 10 0 0 0 0-20zm-1 17.9A8 8 0 0 1 4.1 13H8c.2 2.6 1.2 4.9 3 6.9zM8 11H4.1A8 8 0 0 1 11 4.1C9.2 6.1 8.2 8.4 8 11zm2 0c.2-2.3 1-4.3 2-5.8 1 1.5 1.8 3.5 2 5.8zm0 2h4c-.2 2.3-1 4.3-2 5.8-1-1.5-1.8-3.5-2-5.8zm3 6.9c1.8-2 2.8-4.3 3-6.9h3.9a8 8 0 0 1-6.9 6.9zM16 11c-.2-2.6-1.2-4.9-3-6.9a8 8 0 0 1 6.9 6.9z"/></svg>www.brightloopservice.ca</li>
    </ul>

    <p class="tagline-band">When Your Gym Gear Stops Working Out, Our Techs Step Right In!</p>
  </section>

  <section class="card card--back">
    <div class="back-brand">
      <span class="back-brand__dot"></span>
      <span class="back-brand__name">Brightloop Service</span>
    </div>
    <p class="back-url">WWW.BRIGHTLOOPSERVICE.CA</p>
  </section>
</main>
</body>
</html>
```